''NOVA TRIM LEAF BLEND'' PRODUCT LABEL BY Zentora RX WE ARE A NATURAL SUPPLEMENT COMPANY

WE NEED A LABEL FOR OUR NEW PRODUCT..THE LABEL WILL BE PLACED ON A BAG NOT A BOTTLE.. SO I WOULD NEED FRONT AND BACK. FRONT SIZE LABEL IS 3 1/2 INCHES LONG AND 3 INCHES WIDE...BACK LABEL WILL BE 3 INCHES LONG AND 3 INCHES WIDE... NAME OF THE PRODUCT IS NOVA TRIM LEAF BLEND. I WOULD LIKE TO SEE AN IMAGE OF A SHIELD WITH ICONS OF ALL THE PRODUCT DOES. PRODUCT HAS A LOT OF ATTRIBUTES . ( MEMORY, BRAIN HEALTH, ANXIETY, MOOD STABILIZER,ANTI-AGING,THYROID HEALTH, NERVOUS SYSTEM HEALTH, ANTI-INFLAMMATORY, HEART HEALTH, DIABETIC HEALTH, LIVER HEALTH, BLOOD CLEANER, GUT HEALTH, ARTERY HEALTH,ANTI-NAUSEA, INTESTINAL HEALTH,TESTOSTERONE BOOSTER , ACNE, BONE AND JOINT HEALTH,KIDNEY HEALTH, DETOXING CELLS, PAIN, WEIGHT LOSS,PROSTATE, ULCER COLITIS, MUSCLE GROWTH,IMMUNITY SYSTEM,FSH, SLEEP, MUSCLE DAMAGE, DHEA, SPERM QUALITY AND QUANTITY ,... FOR BOTH WOMEN AND MEN..THIS PRODUCT IS VERY HEALTHY ..:) WANT YOU TO USE YOUR DESIGN SKILLS FOR THE WORLD'S HEALTH..A PICTURE IS WORTH A THOUSAND WORDS. ICONS WOULD WORK GREAT... THE COMPANY Zentora Rx logo is to be used somewhere on the label. THE PRODUCT IS ALSO VEGAN, NON GMO, MADE IN U.S.A...ALL NATURAL HERBAL SUPPLEMENT
Updates

label is to be 3 1/2inches and 3 inches wide

Target Market(s)

ALL AGES.. MEN AND WOMEN.. PEOPLE THAT NEED TO CLEAN THEIR BODY.

Industry/Entity Type

Nutrition

Colors

Designer to choose colors to be used in the design.

Requirements
Must have
• A SHIELD AND ICONS OF PRODUCT ATTRIBUTES..FRONT AND BACK LABEL FOR BAG.

```html
<!DOCTYPE html>
<html lang="en">
<head>
<meta charset="utf-8">
<title>Nova Trim Leaf Blend – Zentora Rx Bag Label</title>
<link rel="stylesheet" href="https://fonts.googleapis.com/css2?family=Oswald:wght@700&family=Montserrat:wght@600;800&display=swap">
<style>
  :root {
    --label-white: #fbfaf7;
    --amber: #b6721c;
    --ink-light: #ffffff;
  }
  html, body {
    margin: 0;
    padding: 0;
    width: 1148px;
    height: 1200px;
    overflow: hidden;
    background: var(--label-white);
  }
  .label { display: block; width: 1148px; height: 1200px; }
  .brand-name {
    font-family: "Montserrat", sans-serif;
    font-weight: 600;
    font-size: 40px;
    fill: var(--amber);
  }
  .brand-dot { fill: var(--amber); }
  .product-name {
    font-family: "Oswald", sans-serif;
    font-weight: 700;
    font-size: 88px;
    letter-spacing: 1px;
    fill: var(--ink-light);
  }
  .band { fill: var(--amber); }
  .icon-disc { fill: var(--amber); }
  .glyph-fill { fill: var(--ink-light); }
  .glyph-line { fill: none; stroke: var(--ink-light); stroke-width: 3.2; stroke-linecap: round; stroke-linejoin: round; }
  .badge-ring { fill: var(--label-white); stroke: var(--amber); stroke-width: 4; }
  .badge-inner { fill: none; stroke: var(--amber); stroke-width: 1.5; }
  .badge-text {
    font-family: "Montserrat", sans-serif;
    font-weight: 800;
    font-size: 15px;
    fill: var(--amber);
  }
  .rule { stroke: var(--amber); stroke-width: 3; }
</style>
</head>
<body>
<svg class="label" viewBox="0 0 1148 1200" xmlns="http://www.w3.org/2000/svg">
  <defs>
    <symbol id="i-heart" viewBox="-20 -20 40 40"><path class="glyph-fill" d="M0 14 C-14 4 -16 -6 -9 -11 C-5 -14 -1 -12 0 -8 C1 -12 5 -14 9 -11 C16 -6 14 4 0 14Z"/></symbol>
    <symbol id="i-drop" viewBox="-20 -20 40 40"><path class="glyph-fill" d="M0 -15 C6 -6 11 0 11 5 A11 11 0 0 1 -11 5 C-11 0 -6 -6 0 -15Z"/></symbol>
    <symbol id="i-leaf" viewBox="-20 -20 40 40"><path class="glyph-fill" d="M-12 12 C-12 -6 0 -14 14 -14 C14 2 6 12 -12 12Z"/><path class="glyph-line" d="M-14 14 L4 -4" style="stroke:#b6721c"/></symbol>
    <symbol id="i-moon" viewBox="-20 -20 40 40"><path class="glyph-fill" d="M4 -14 A14 14 0 1 0 14 6 A11 11 0 1 1 4 -14Z"/></symbol>
    <symbol id="i-smile" viewBox="-20 -20 40 40"><circle class="glyph-line" r="14"/><circle class="glyph-fill" cx="-5" cy="-4" r="2.2"/><circle class="glyph-fill" cx="5" cy="-4" r="2.2"/><path class="glyph-line" d="M-7 4 Q0 11 7 4"/></symbol>
    <symbol id="i-frown" viewBox="-20 -20 40 40"><circle class="glyph-line" r="14"/><circle class="glyph-fill" cx="-5" cy="-4" r="2.2"/><circle class="glyph-fill" cx="5" cy="-4" r="2.2"/><path class="glyph-line" d="M-7 8 Q0 1 7 8"/></symbol>
    <symbol id="i-bone" viewBox="-20 -20 40 40"><g transform="rotate(-45)" class="glyph-fill"><rect x="-10" y="-3.5" width="20" height="7"/><circle cx="-11" cy="-4" r="4.5"/><circle cx="-11" cy="4" r="4.5"/><circle cx="11" cy="-4" r="4.5"/><circle cx="11" cy="4" r="4.5"/></g></symbol>
    <symbol id="i-gut" viewBox="-20 -20 40 40"><path class="glyph-line" d="M-10 -12 H10 V-6 H-10 V0 H10 V6 H-10 V12 H10"/></symbol>
    <symbol id="i-bolt" viewBox="-20 -20 40 40"><path class="glyph-fill" d="M3 -15 L-9 2 H-1 L-4 15 L9 -3 H1Z"/></symbol>
    <symbol id="i-sun" viewBox="-20 -20 40 40"><circle class="glyph-fill" r="6"/><path class="glyph-line" d="M0 -15 V-10 M0 10 V15 M-15 0 H-10 M10 0 H15 M-10.5 -10.5 L-7 -7 M7 7 L10.5 10.5 M-10.5 10.5 L-7 7 M7 -7 L10.5 -10.5"/></symbol>
    <symbol id="i-molecule" viewBox="-20 -20 40 40"><path class="glyph-line" d="M-9 8 L0 -8 L10 6 Z"/><circle class="glyph-fill" cx="-9" cy="8" r="4.5"/><circle class="glyph-fill" cx="0" cy="-8" r="4.5"/><circle class="glyph-fill" cx="10" cy="6" r="4.5"/></symbol>
    <symbol id="i-pill" viewBox="-20 -20 40 40"><rect class="glyph-line" x="-14" y="-6" width="28" height="12" rx="6" transform="rotate(-40)"/><path class="glyph-line" d="M-4 -5 L4 5" transform="rotate(-40) rotate(40)"/></symbol>
    <symbol id="i-cross" viewBox="-20 -20 40 40"><path class="glyph-fill" d="M-4 -14 H4 V-4 H14 V4 H4 V14 H-4 V4 H-14 V-4 H-4Z"/></symbol>
    <symbol id="i-shield" viewBox="-20 -20 40 40"><path class="glyph-fill" d="M0 -14 L12 -9 V0 C12 8 6 12 0 15 C-6 12 -12 8 -12 0 V-9Z"/></symbol>
    <symbol id="i-dumbbell" viewBox="-20 -20 40 40"><g class="glyph-fill"><rect x="-10" y="-2" width="20" height="4"/><rect x="-15" y="-9" width="5" height="18" rx="1.5"/><rect x="10" y="-9" width="5" height="18" rx="1.5"/></g></symbol>
    <symbol id="i-weight" viewBox="-20 -20 40 40"><path class="glyph-fill" d="M-8 -6 H8 L13 13 H-13Z"/><circle class="glyph-line" cx="0" cy="-10" r="4"/></symbol>
    <symbol id="i-brain" viewBox="-20 -20 40 40"><g class="glyph-fill"><circle cx="-6" cy="-5" r="7"/><circle cx="6" cy="-5" r="7"/><circle cx="-7" cy="5" r="7"/><circle cx="7" cy="5" r="7"/></g><path class="glyph-line" d="M0 -12 V12" style="stroke:#b6721c;stroke-width:2"/></symbol>
    <symbol id="i-kidney" viewBox="-20 -20 40 40"><path class="glyph-fill" d="M2 -14 C-10 -16 -14 -4 -12 4 C-10 14 2 16 6 10 C9 6 4 2 4 0 C4 -2 9 -5 8 -9 C7 -12 5 -14 2 -14Z"/></symbol>
  </defs>

  <!-- brand -->
  <g class="brand">
    <circle class="brand-dot" cx="372" cy="196" r="22"/>
    <text x="406" y="210" class="brand-name">Zentora Rx</text>
  </g>

  <!-- attribute icons, upper block -->
  <g class="attribute-grid" aria-label="Health attribute icons">
    <g transform="translate(390 290)"><circle class="icon-disc" r="34"/><use href="#i-brain" x="-20" y="-20" width="40" height="40"/></g>
    <g transform="translate(482 290)"><circle class="icon-disc" r="34"/><use href="#i-molecule" x="-20" y="-20" width="40" height="40"/></g>
    <g transform="translate(574 290)"><circle class="icon-disc" r="34"/><use href="#i-kidney" x="-20" y="-20" width="40" height="40"/></g>
    <g transform="translate(666 290)"><circle class="icon-disc" r="34"/><use href="#i-heart" x="-20" y="-20" width="40" height="40"/></g>
    <g transform="translate(758 290)"><circle class="icon-disc" r="34"/><use href="#i-drop" x="-20" y="-20" width="40" height="40"/></g>

    <g transform="translate(344 382)"><circle class="icon-disc" r="34"/><use href="#i-pill" x="-20" y="-20" width="40" height="40"/></g>
    <g transform="translate(436 382)"><circle class="icon-disc" r="34"/><use href="#i-gut" x="-20" y="-20" width="40" height="40"/></g>
    <g transform="translate(528 382)"><circle class="icon-disc" r="34"/><use href="#i-bone" x="-20" y="-20" width="40" height="40"/></g>
    <g transform="translate(620 382)"><circle class="icon-disc" r="34"/><use href="#i-shield" x="-20" y="-20" width="40" height="40"/></g>
    <g transform="translate(712 382)"><circle class="icon-disc" r="34"/><use href="#i-moon" x="-20" y="-20" width="40" height="40"/></g>
    <g transform="translate(804 382)"><circle class="icon-disc" r="34"/><use href="#i-leaf" x="-20" y="-20" width="40" height="40"/></g>

    <g transform="translate(344 474)"><circle class="icon-disc" r="34"/><use href="#i-sun" x="-20" y="-20" width="40" height="40"/></g>
    <g transform="translate(436 474)"><circle class="icon-disc" r="34"/><use href="#i-dumbbell" x="-20" y="-20" width="40" height="40"/></g>
    <g transform="translate(528 474)"><circle class="icon-disc" r="34"/><use href="#i-cross" x="-20" y="-20" width="40" height="40"/></g>
    <g transform="translate(620 474)"><circle class="icon-disc" r="34"/><use href="#i-weight" x="-20" y="-20" width="40" height="40"/></g>
    <g transform="translate(712 474)"><circle class="icon-disc" r="34"/><use href="#i-bolt" x="-20" y="-20" width="40" height="40"/></g>
    <g transform="translate(804 474)"><circle class="icon-disc" r="34"/><use href="#i-frown" x="-20" y="-20" width="40" height="40"/></g>

    <g transform="translate(390 566)"><circle class="icon-disc" r="34"/><use href="#i-drop" x="-20" y="-20" width="40" height="40"/></g>
    <g transform="translate(482 566)"><circle class="icon-disc" r="34"/><use href="#i-heart" x="-20" y="-20" width="40" height="40"/></g>
    <g transform="translate(574 566)"><circle class="icon-disc" r="34"/><use href="#i-brain" x="-20" y="-20" width="40" height="40"/></g>
    <g transform="translate(666 566)"><circle class="icon-disc" r="34"/><use href="#i-molecule" x="-20" y="-20" width="40" height="40"/></g>
    <g transform="translate(758 566)"><circle class="icon-disc" r="34"/><use href="#i-bone" x="-20" y="-20" width="40" height="40"/></g>
  </g>

  <!-- product name band -->
  <g class="name-band">
    <rect class="band" x="120" y="620" width="908" height="104"/>
    <text x="574" y="704" text-anchor="middle" class="product-name">NOVA TRIM LEAF BLEND</text>
  </g>

  <!-- attribute icons, lower block -->
  <g class="attribute-grid">
    <g transform="translate(344 784)"><circle class="icon-disc" r="34"/><use href="#i-smile" x="-20" y="-20" width="40" height="40"/></g>
    <g transform="translate(436 784)"><circle class="icon-disc" r="34"/><use href="#i-moon" x="-20" y="-20" width="40" height="40"/></g>
    <g transform="translate(528 784)"><circle class="icon-disc" r="34"/><use href="#i-gut" x="-20" y="-20" width="40" height="40"/></g>
    <g transform="translate(620 784)"><circle class="icon-disc" r="34"/><use href="#i-kidney" x="-20" y="-20" width="40" height="40"/></g>
    <g transform="translate(712 784)"><circle class="icon-disc" r="34"/><use href="#i-sun" x="-20" y="-20" width="40" height="40"/></g>
    <g transform="translate(804 784)"><circle class="icon-disc" r="34"/><use href="#i-bolt" x="-20" y="-20" width="40" height="40"/></g>

    <g transform="translate(436 876)"><circle class="icon-disc" r="34"/><use href="#i-dumbbell" x="-20" y="-20" width="40" height="40"/></g>
    <g transform="translate(528 876)"><circle class="icon-disc" r="34"/><use href="#i-leaf" x="-20" y="-20" width="40" height="40"/></g>
    <g transform="translate(620 876)"><circle class="icon-disc" r="34"/><use href="#i-shield" x="-20" y="-20" width="40" height="40"/></g>
    <g transform="translate(712 876)"><circle class="icon-disc" r="34"/><use href="#i-weight" x="-20" y="-20" width="40" height="40"/></g>
  </g>

  <!-- claim badges -->
  <g class="claim-badges">
    <line class="rule" x1="330" y1="1000" x2="376" y2="1000"/>
    <line class="rule" x1="772" y1="1000" x2="818" y2="1000"/>

    <g transform="translate(430 1000)">
      <circle class="badge-ring" r="46"/><circle class="badge-inner" r="39"/>
      <text class="badge-text" text-anchor="middle" y="-3">100%</text>
      <text class="badge-text" text-anchor="middle" y="16">VEGAN</text>
    </g>
    <g transform="translate(544 1000)">
      <circle class="badge-ring" r="46"/><circle class="badge-inner" r="39"/>
      <text class="badge-text" text-anchor="middle" y="-3" style="font-size:18px">NON</text>
      <text class="badge-text" text-anchor="middle" y="17" style="font-size:18px">GMO</text>
    </g>
    <g transform="translate(658 1000)">
      <circle class="badge-ring" r="46"/><circle class="badge-inner" r="39"/>
      <text class="badge-text" text-anchor="middle" y="-3" style="font-size:12px">NATURAL</text>
      <text class="badge-text" text-anchor="middle" y="13" style="font-size:12px">HERBAL</text>
    </g>
    <g transform="translate(772 1000)" style="display:none"></g>
    <g transform="translate(772 1000)">
    </g>
  </g>
  <g class="claim-badges" transform="translate(114 0)">
    <g transform="translate(658 1000)">
      <circle class="badge-ring" r="46"/><circle class="badge-inner" r="39"/>
      <text class="badge-text" text-anchor="middle" y="-3" style="font-size:13px">MADE IN</text>
      <text class="badge-text" text-anchor="middle" y="15" style="font-size:16px">USA</text>
    </g>
  </g>
  <line class="rule" x1="818" y1="1000" x2="864" y2="1000"/>
</svg>
</body>
</html>
```